Brookmere Osteopathy flyer

I want a clean clear DL flyer (but also want an A4 poster) promoting a new Osteopathic business in a semi rural area in Tasmania (Australia).
It can have pictures like the examples attached to show people what Osteopathy is (its like Chiropractic and physiotherapy).
I am the sole practioner and am male, so any pictures would be best to be a white male if possible.
I've attached some wording, you can use all, or none of it
I don't have a phone number for the business yet
info@brookmereosteopathy.example
www.brookmereosteopathy.example
Target Market(s)
Australians, from tradies, professionals, babies to retired people
Industry/Entity Type
Health
Look and feel

```html
<!DOCTYPE html>
<html lang="en">
<head>
<meta charset="utf-8">
<title>Brookmere Osteopathy – Flyer</title>
<link rel="stylesheet" href="https://fonts.googleapis.com/css2?family=Poppins:ital,wght@0,500;0,600;0,700;1,400;1,700&display=swap">
<style>
  :root {
    --page-bg: #505050;
    --white: #ffffff;
    --brand-blue: #0a77b8;
    --ring-blue: #1192d4;
    --brand-orange: #f58e33;
    --ink: #1e1e1e;
    --wash: #eef5fb;
  }
  * { margin: 0; padding: 0; box-sizing: border-box; }
  html, body { width: 678px; height: 1200px; overflow: hidden; background: var(--page-bg); }
  body { font-family: "Poppins", sans-serif; color: var(--ink); }

  .flyer {
    position: absolute; left: 82px; top: 56px;
    width: 513px; height: 1090px; overflow: hidden;
    background: linear-gradient(180deg, var(--white) 40%, var(--wash) 100%);
  }
  .flyer-shapes { position: absolute; inset: 0; width: 513px; height: 1090px; }

  .brand-badge {
    position: absolute; left: 40px; top: 267px; width: 206px; height: 206px;
    border-radius: 50%; background: var(--white);
    box-shadow: 0 4px 10px rgba(0,0,0,.15);
    display: flex; align-items: center; justify-content: center; text-align: center;
  }
  .brand-name { color: var(--ring-blue); font-weight: 600; font-size: 21px; line-height: 1.2; }

  .reasons { position: absolute; left: 42px; top: 486px; }
  .reasons-title { color: var(--brand-blue); font-weight: 700; font-size: 21.5px; line-height: 23px; letter-spacing: -.2px; }
  .reasons-list { list-style: none; margin-top: 9px; }
  .reasons-list li { display: flex; align-items: center; height: 26.2px; font-weight: 500; font-size: 15.8px; letter-spacing: -.2px; }
  .tick { width: 18px; height: 18px; margin-right: 7px; flex: none; }

  .summary {
    position: absolute; left: 37px; top: 826px; width: 450px;
    font-style: italic; font-size: 15px; line-height: 21px; letter-spacing: -.2px;
  }
  .summary strong { font-weight: 700; }

  .call-button {
    position: absolute; left: 101px; top: 979px; width: 306px; height: 36px;
    border-radius: 18px; background: var(--brand-orange); color: var(--white);
    font-weight: 600; font-size: 20px; display: flex; align-items: center; justify-content: center;
  }
  .address {
    position: absolute; left: 0; top: 1024px; width: 513px; text-align: center;
    color: var(--white); font-weight: 500; font-size: 17px;
    display: flex; align-items: center; justify-content: center; gap: 4px;
  }
  .contact-row {
    position: absolute; left: 0; top: 1053px; width: 513px;
    display: flex; justify-content: center; gap: 12px;
    color: var(--white); font-weight: 500; font-size: 11.5px;
  }
  .contact-row span { display: flex; align-items: center; gap: 4px; }
  .icon { width: 13px; height: 13px; flex: none; }
</style>
</head>
<body>
<main class="flyer">
  <svg class="flyer-shapes" viewBox="0 0 513 1090" aria-hidden="false">
    <defs>
      <linearGradient id="hero-tone" x1="0" y1="0" x2="1" y2="1">
        <stop offset="0" stop-color="#f1efec"/>
        <stop offset=".45" stop-color="#d9a98a"/>
        <stop offset="1" stop-color="#b98264"/>
      </linearGradient>
      <radialGradient id="detail-tone" cx=".5" cy=".5" r=".6">
        <stop offset="0" stop-color="#e6b898"/>
        <stop offset="1" stop-color="#c9927a"/>
      </radialGradient>
    </defs>

    <!-- swooshes under hero -->
    <path d="M0,186 C80,330 200,420 330,432 L330,452 C190,455 60,400 0,340 Z" fill="var(--brand-orange)"/>
    <path d="M0,196 C80,330 240,420 513,360 V392 C260,450 80,360 0,232 Z" fill="var(--brand-blue)"/>

    <!-- hero photograph area -->
    <path role="img" aria-label="Photo: osteopath treating a patient's back on a treatment table"
          d="M0,0 H513 V335 C420,380 330,395 250,385 C150,370 60,290 0,186 Z"
          fill="url(#hero-tone)" stroke="var(--white)" stroke-width="5"/>

    <!-- treatment detail circles -->
    <circle cx="405" cy="450" r="93" fill="var(--ring-blue)"/>
    <circle cx="405" cy="450" r="81" fill="var(--white)"/>
    <circle role="img" aria-label="Photo: hands applying pressure to a patient's upper back" cx="405" cy="450" r="78" fill="url(#detail-tone)"/>

    <circle cx="405" cy="647" r="93" fill="var(--ring-blue)"/>
    <circle cx="405" cy="647" r="81" fill="var(--white)"/>
    <circle role="img" aria-label="Photo: practitioner treating a patient's shoulder blade" cx="405" cy="647" r="78" fill="url(#detail-tone)"/>

    <!-- footer band -->
    <path d="M0,1005 Q256,833 513,1005 L513,1030 Q256,850 0,1030 Z" fill="var(--brand-orange)"/>
    <path d="M0,1035 Q256,853 513,1035 V1090 H0 Z" fill="var(--brand-blue)"/>
  </svg>

  <div class="brand-badge">
    <p class="brand-name">Brookmere<br>Osteopathy</p>
  </div>

  <section class="reasons">
    <h1 class="reasons-title">Common reasons<br>people visit an osteopath</h1>
    <ul class="reasons-list">
      <li><svg class="tick" viewBox="0 0 18 18"><circle cx="9" cy="9" r="9" fill="var(--brand-orange)"/><path d="M5 9.3l2.7 2.6L13 6.5" fill="none" stroke="#fff" stroke-width="2" stroke-linecap="round" stroke-linejoin="round"/></svg>Back / neck pain</li>
      <li><svg class="tick" viewBox="0 0 18 18"><circle cx="9" cy="9" r="9" fill="var(--brand-orange)"/><path d="M5 9.3l2.7 2.6L13 6.5" fill="none" stroke="#fff" stroke-width="2" stroke-linecap="round" stroke-linejoin="round"/></svg>Headaches / migraines</li>
      <li><svg class="tick" viewBox="0 0 18 18"><circle cx="9" cy="9" r="9" fill="var(--brand-orange)"/><path d="M5 9.3l2.7 2.6L13 6.5" fill="none" stroke="#fff" stroke-width="2" stroke-linecap="round" stroke-linejoin="round"/></svg>Joint and muscle pain</li>
      <li><svg class="tick" viewBox="0 0 18 18"><circle cx="9" cy="9" r="9" fill="var(--brand-orange)"/><path d="M5 9.3l2.7 2.6L13 6.5" fill="none" stroke="#fff" stroke-width="2" stroke-linecap="round" stroke-linejoin="round"/></svg>Pregnancy-related discomfort</li>
      <li><svg class="tick" viewBox="0 0 18 18"><circle cx="9" cy="9" r="9" fill="var(--brand-orange)"/><path d="M5 9.3l2.7 2.6L13 6.5" fill="none" stroke="#fff" stroke-width="2" stroke-linecap="round" stroke-linejoin="round"/></svg>Disc related issues</li>
      <li><svg class="tick" viewBox="0 0 18 18"><circle cx="9" cy="9" r="9" fill="var(--brand-orange)"/><path d="M5 9.3l2.7 2.6L13 6.5" fill="none" stroke="#fff" stroke-width="2" stroke-linecap="round" stroke-linejoin="round"/></svg>Sciatica</li>
      <li><svg class="tick" viewBox="0 0 18 18"><circle cx="9" cy="9" r="9" fill="var(--brand-orange)"/><path d="M5 9.3l2.7 2.6L13 6.5" fill="none" stroke="#fff" stroke-width="2" stroke-linecap="round" stroke-linejoin="round"/></svg>Plantar fasciitis</li>
      <li><svg class="tick" viewBox="0 0 18 18"><circle cx="9" cy="9" r="9" fill="var(--brand-orange)"/><path d="M5 9.3l2.7 2.6L13 6.5" fill="none" stroke="#fff" stroke-width="2" stroke-linecap="round" stroke-linejoin="round"/></svg>Tendonitis / Bursitis</li>
      <li><svg class="tick" viewBox="0 0 18 18"><circle cx="9" cy="9" r="9" fill="var(--brand-orange)"/><path d="M5 9.3l2.7 2.6L13 6.5" fill="none" stroke="#fff" stroke-width="2" stroke-linecap="round" stroke-linejoin="round"/></svg>Adhesive capsulitis (frozen shoulder)</li>
      <li><svg class="tick" viewBox="0 0 18 18"><circle cx="9" cy="9" r="9" fill="var(--brand-orange)"/><path d="M5 9.3l2.7 2.6L13 6.5" fill="none" stroke="#fff" stroke-width="2" stroke-linecap="round" stroke-linejoin="round"/></svg>Tennis / Golfers elbow</li>
    </ul>
  </section>

  <p class="summary">Osteopaths use a combination of <strong>joint manipulation</strong>, <strong>targeted deep tissue massage</strong> and <strong>stretching</strong> to improve <strong>function, relieve pain</strong> and support the body’s ability to <strong>heal itself.</strong></p>

  <div class="call-button">Call us Today! 123-456-780</div>

  <p class="address">
    <svg class="icon" viewBox="0 0 14 18" style="width:13px;height:17px"><path d="M7 1a6 6 0 0 0-6 6c0 4.5 6 10 6 10s6-5.5 6-10a6 6 0 0 0-6-6z" fill="none" stroke="var(--brand-orange)" stroke-width="2"/><circle cx="7" cy="7" r="2.2" fill="var(--brand-orange)"/></svg>
    48 Willow Creek Road, Brookmere
  </p>

  <div class="contact-row">
    <span><svg class="icon" viewBox="0 0 14 14"><g fill="none" stroke="var(--brand-orange)" stroke-width="1"><circle cx="7" cy="7" r="6"/><ellipse cx="7" cy="7" rx="2.6" ry="6"/><path d="M1 7h12M2 4h10M2 10h10"/></g></svg>www.brookmereosteopathy.example</span>
    <span><svg class="icon" viewBox="0 0 16 12" style="width:15px;height:11px"><g fill="none" stroke="var(--brand-orange)" stroke-width="1.1"><rect x=".6" y=".6" width="14.8" height="10.8"/><path d="M.6.6L8 7l7.4-6.4M.6 11.4l5.3-5.2M15.4 11.4l-5.3-5.2"/></g></svg>info@brookmereosteopathy.example</span>
  </div>
</main>
</body>
</html>
```